Quran Jar

So I need help designing bespoke jars which will contain religious quotes.

So there will be three jars in total sold either individually or in two or as a three.

Each Jar will have different contents and preferably a different colour scheme.

I want the packaging to be customised with my branding and logo and to make the product stand out I am thinking of packing it further in a cotton bag with my branding.

```html
<!DOCTYPE html>
<html lang="en">
<head>
<meta charset="utf-8">
<title>Serene Verses – Jar Labels</title>
<link rel="stylesheet" href="https://fonts.googleapis.com/css2?family=Tinos:wght@400;700&display=swap">
<style>
  :root{
    --gold:#f6b21c;
    --gold-deep:#e59a12;
    --white:#ffffff;
    --sad-sky:#fbe7b4;
    --sad-rim:#f2a85a;
    --sad-top:#0f58a6;
    --sad-bottom:#272a6c;
    --lonely-sky:#fdf1c2;
    --lonely-rim:#0b4e6e;
    --lonely-fill:#0986a3;
    --lonely-frame:#4fb3c9;
    --thankful-bg:#063f22;
    --thankful-fill:#0a4a26;
    --thankful-line:#f2a21a;
  }
  html,body{margin:0;padding:0;overflow:hidden;background:#ffffff;}
  .sheet{position:relative;width:1200px;height:2267px;overflow:hidden;background:#ffffff;}
  .label{position:absolute;left:0;width:1200px;display:block;}
  .label--sad{top:0;height:731px;}
  .label--lonely{top:764px;height:725px;}
  .label--thankful{top:1527px;height:740px;}
  .brand-name{font-family:"Tinos",serif;font-weight:400;fill:var(--gold);}
  .brand-line{font-family:"Tinos",serif;font-weight:400;fill:var(--gold);letter-spacing:3px;}
  .kicker{font-family:"Tinos",serif;font-weight:700;fill:var(--white);}
  .headline{font-family:"Tinos",serif;font-weight:400;fill:var(--white);letter-spacing:2px;}
  .emotion{font-family:"Tinos",serif;font-weight:400;fill:var(--white);letter-spacing:3px;}
  .verse{font-family:"Tinos",serif;font-weight:400;fill:var(--white);}
  .verse-source{font-family:"Tinos",serif;font-weight:400;fill:var(--white);}
  .rule{stroke:var(--white);stroke-width:1.5;}
</style>
</head>
<body>
<main class="sheet">

  <!-- Label: SAD -->
  <svg class="label label--sad" viewBox="0 0 1200 731" xmlns="http://www.w3.org/2000/svg">
    <defs>
      <linearGradient id="sad-fill" x1="0" y1="0" x2="0" y2="1">
        <stop offset="0" stop-color="var(--sad-top)"/>
        <stop offset="1" stop-color="var(--sad-bottom)"/>
      </linearGradient>
    </defs>
    <rect class="pattern-backdrop" width="1200" height="731" fill="var(--sad-sky)" role="img" aria-label="Soft gold geometric star pattern background"/>
    <path class="arch-rim" d="M0 731V540C0 450 50 410 100 385C120 320 165 290 235 270C285 252 320 240 340 210C370 150 430 115 510 85C560 65 592 45 600 22C608 45 640 65 690 85C770 115 830 150 860 210C880 240 915 252 965 270C1035 290 1080 320 1100 385C1150 410 1200 450 1200 540V731Z" fill="var(--sad-rim)"/>
    <path class="arch-fill" d="M0 731V575C0 485 60 445 120 420C140 355 180 325 250 305C300 288 335 275 360 245C390 185 445 150 520 120C568 100 594 80 600 58C606 80 632 100 680 120C755 150 810 185 840 245C865 275 900 288 950 305C1020 325 1060 355 1080 420C1140 445 1200 485 1200 575V731Z" fill="url(#sad-fill)"/>
    <g role="img" aria-label="Hanging golden lanterns on bead chains">
      <line x1="130" y1="0" x2="130" y2="300" stroke="var(--gold-deep)" stroke-width="6" stroke-dasharray="6 10"/>
      <line x1="257" y1="0" x2="257" y2="165" stroke="var(--gold-deep)" stroke-width="6" stroke-dasharray="6 10"/>
      <rect x="222" y="165" width="72" height="150" rx="10" fill="var(--gold)"/>
      <rect x="98" y="300" width="68" height="145" rx="10" fill="var(--gold)"/>
      <line x1="1070" y1="0" x2="1070" y2="300" stroke="var(--gold-deep)" stroke-width="6" stroke-dasharray="6 10"/>
      <line x1="930" y1="0" x2="930" y2="205" stroke="var(--gold-deep)" stroke-width="6" stroke-dasharray="6 10"/>
      <rect x="895" y="205" width="72" height="150" rx="10" fill="var(--gold)"/>
      <rect x="1036" y="300" width="68" height="145" rx="10" fill="var(--gold)"/>
    </g>
    <circle cx="600" cy="195" r="48" fill="var(--gold)"/>
    <text class="brand-name" x="600" y="317" text-anchor="middle" font-size="56">Serene Verses</text>
    <text class="brand-line" x="600" y="341" text-anchor="middle" font-size="14">VERSES FOR THE HEART</text>
    <line class="rule" x1="438" y1="364" x2="759" y2="364"/>
    <text class="kicker" x="600" y="402" text-anchor="middle" font-size="28">A MESSAGE FOR EVERY EMOTION</text>
    <line class="rule" x1="438" y1="417" x2="759" y2="417"/>
    <text class="headline" x="600" y="480" text-anchor="middle" font-size="60">READ ME WHEN...</text>
    <line class="rule" x1="520" y1="523" x2="680" y2="523"/>
    <line class="rule" x1="520" y1="588" x2="680" y2="588"/>
    <line class="rule" x1="333" y1="557" x2="500" y2="557"/>
    <line class="rule" x1="700" y1="557" x2="868" y2="557"/>
    <text class="emotion" x="600" y="575" text-anchor="middle" font-size="55">SAD</text>
    <text class="verse" x="600" y="633" text-anchor="middle" font-size="24">“DO YOU NOT SEE HOW ALLAH COMPARES A GOOD WORD TO A GOOD TREE?</text>
    <text class="verse" x="600" y="662" text-anchor="middle" font-size="24">ITS ROOT IS FIRM AND ITS BRANCHES REACH THE SKY.”</text>
    <text class="verse-source" x="600" y="700" text-anchor="middle" font-size="18">(SURAH IBRAHIM 14:24).</text>
  </svg>

  <!-- Label: LONELY -->
  <svg class="label label--lonely" viewBox="0 0 1200 725" xmlns="http://www.w3.org/2000/svg">
    <rect class="pattern-backdrop" width="1200" height="725" fill="var(--lonely-sky)" role="img" aria-label="Pale cream geometric star pattern background"/>
    <rect x="12" y="12" width="1176" height="713" fill="none" stroke="var(--lonely-frame)" stroke-width="4"/>
    <path class="arch-rim" d="M60 725V440C60 380 95 345 150 325C175 265 215 235 285 220C330 210 345 200 360 170C390 110 470 85 545 75C575 60 592 38 600 25C608 38 625 60 655 75C730 85 810 110 840 170C855 200 870 210 915 220C985 235 1025 265 1050 325C1105 345 1140 380 1140 440V725Z" fill="var(--lonely-rim)"/>
    <path class="arch-fill" d="M78 725V448C78 395 110 365 162 345C187 285 225 258 292 243C340 232 358 220 374 190C402 130 478 105 552 95C580 80 594 62 600 48C606 62 620 80 648 95C722 105 798 130 826 190C842 220 860 232 908 243C975 258 1013 285 1038 345C1090 365 1122 395 1122 448V725Z" fill="var(--lonely-fill)"/>
    <g role="img" aria-label="Hanging ornate golden lanterns">
      <line x1="157" y1="0" x2="157" y2="320" stroke="var(--gold-deep)" stroke-width="3"/>
      <line x1="250" y1="0" x2="250" y2="80" stroke="var(--gold-deep)" stroke-width="3"/>
      <rect x="212" y="80" width="76" height="170" rx="14" fill="var(--gold)"/>
      <rect x="112" y="310" width="90" height="190" rx="18" fill="var(--gold)"/>
      <line x1="1043" y1="0" x2="1043" y2="320" stroke="var(--gold-deep)" stroke-width="3"/>
      <line x1="950" y1="0" x2="950" y2="80" stroke="var(--gold-deep)" stroke-width="3"/>
      <rect x="912" y="80" width="76" height="170" rx="14" fill="var(--gold)"/>
      <rect x="998" y="310" width="90" height="190" rx="18" fill="var(--gold)"/>
    </g>
    <circle cx="598" cy="182" r="62" fill="var(--gold)"/>
    <text class="brand-name" x="598" y="318" text-anchor="middle" font-size="64">Serene Verses</text>
    <text class="brand-line" x="598" y="346" text-anchor="middle" font-size="15">VERSES FOR THE HEART</text>
    <text class="kicker" x="600" y="402" text-anchor="middle" font-size="28">A MESSAGE FOR EVERY EMOTION</text>
    <line class="rule" x1="443" y1="420" x2="762" y2="420"/>
    <text class="headline" x="626" y="487" text-anchor="middle" font-size="60">READ ME WHEN...</text>
    <line class="rule" x1="474" y1="531" x2="727" y2="531"/>
    <line class="rule" x1="474" y1="602" x2="727" y2="602"/>
    <line class="rule" x1="286" y1="567" x2="460" y2="567"/>
    <line class="rule" x1="745" y1="567" x2="918" y2="567"/>
    <text class="emotion" x="600" y="587" text-anchor="middle" font-size="57">LONELY</text>
    <text class="verse" x="600" y="646" text-anchor="middle" font-size="21">“DO YOU NOT SEE HOW ALLAH COMPARES A GOOD WORD TO A GOOD TREE?</text>
    <text class="verse" x="600" y="670" text-anchor="middle" font-size="21">ITS ROOT IS FIRM AND ITS BRANCHES REACH THE SKY.”</text>
    <text class="verse-source" x="600" y="700" text-anchor="middle" font-size="16">(SURAH IBRAHIM 14:24).</text>
  </svg>

  <!-- Label: THANKFUL -->
  <svg class="label label--thankful" viewBox="0 0 1200 740" xmlns="http://www.w3.org/2000/svg">
    <rect class="pattern-backdrop" width="1200" height="740" fill="var(--thankful-bg)" role="img" aria-label="Deep green background with faint geometric pattern"/>
    <path class="arch-fill" d="M40 740V350L220 300C240 180 330 90 420 60C500 35 560 25 600 10C640 25 700 35 780 60C870 90 960 180 980 300L1160 350V740Z" fill="var(--thankful-fill)" stroke="var(--thankful-line)" stroke-width="6"/>
    <path d="M58 740V362L236 314C255 200 342 112 428 82C505 56 562 46 600 32C638 46 695 56 772 82C858 112 945 200 964 314L1142 362V740" fill="none" stroke="var(--white)" stroke-width="2"/>
    <g role="img" aria-label="Hanging golden lanterns with stars on strings">
      <line x1="70" y1="0" x2="70" y2="240" stroke="var(--thankful-line)" stroke-width="3"/>
      <line x1="140" y1="0" x2="140" y2="140" stroke="var(--thankful-line)" stroke-width="3"/>
      <rect x="105" y="140" width="72" height="130" rx="12" fill="var(--gold)"/>
      <rect x="34" y="240" width="70" height="140" rx="12" fill="var(--gold)"/>
      <line x1="1130" y1="0" x2="1130" y2="240" stroke="var(--thankful-line)" stroke-width="3"/>
      <line x1="1060" y1="0" x2="1060" y2="140" stroke="var(--thankful-line)" stroke-width="3"/>
      <rect x="1023" y="140" width="72" height="130" rx="12" fill="var(--gold)"/>
      <rect x="1096" y="240" width="70" height="140" rx="12" fill="var(--gold)"/>
    </g>
    <circle cx="600" cy="70" r="44" fill="var(--gold)"/>
    <text class="brand-name" x="600" y="198" text-anchor="middle" font-size="52">Serene Verses</text>
    <text class="brand-line" x="600" y="222" text-anchor="middle" font-size="13">VERSES FOR THE HEART</text>
    <text class="kicker" x="600" y="293" text-anchor="middle" font-size="28">A MESSAGE FOR EVERY EMOTION</text>
    <line class="rule" x1="443" y1="309" x2="762" y2="309"/>
    <text class="headline" x="600" y="405" text-anchor="middle" font-size="60">READ ME WHEN...</text>
    <line class="rule" x1="443" y1="482" x2="762" y2="482"/>
    <line class="rule" x1="443" y1="553" x2="762" y2="553"/>
    <line class="rule" x1="250" y1="518" x2="420" y2="518"/>
    <line class="rule" x1="780" y1="518" x2="968" y2="518"/>
    <text class="emotion" x="600" y="540" text-anchor="middle" font-size="57">THANKFUL</text>
    <text class="verse" x="600" y="623" text-anchor="middle" font-size="24">“DO YOU NOT SEE HOW ALLAH COMPARES A GOOD WORD TO A GOOD TREE?</text>
    <text class="verse" x="600" y="651" text-anchor="middle" font-size="24">ITS ROOT IS FIRM AND ITS BRANCHES REACH THE SKY.”</text>
    <text class="verse-source" x="600" y="696" text-anchor="middle" font-size="18">(SURAH IBRAHIM 14:24).</text>
  </svg>

</main>
</body>
</html>
```